Fernhale Business Card Design

We are looking for a fresh business card design for our new logo. We would like a business card that is unique but friendly. We are in the window coverings business offering blinds, shutters and shades for homes.

Target Market(s)

Targeting the end-consumer

Industry/Entity Type

Business

Requirements
Must have
• Must have a dedicates space for a photo of our sales person. Must contain our new logo (attached).

```html
<!DOCTYPE html>
<html lang="en">
<head>
<meta charset="utf-8">
<title>Fernhale Business Card</title>
<link rel="stylesheet" href="https://fonts.googleapis.com/css2?family=Lato:wght@700&family=Oswald:wght@500&display=swap">
<style>
  :root {
    --backdrop: #2b1c18;
    --leaf-green: #8cc63f;
    --card-white: #ffffff;
    --ink-green: #8cc63f;
    --photo-tint-light: #eef6e2;
    --photo-tint-dark: #d3e8b5;
  }
  * { margin: 0; padding: 0; box-sizing: border-box; }
  html, body {
    width: 1200px;
    height: 663px;
    overflow: hidden;
    background: var(--backdrop);
  }
  .canvas {
    position: relative;
    width: 1200px;
    height: 663px;
  }
  .card {
    position: absolute;
    top: 188px;
    width: 500px;
    height: 286px;
    box-shadow: 0 6px 18px rgba(0, 0, 0, 0.45);
  }
  .card-front {
    left: 70px;
    background: var(--leaf-green);
  }
  .brand {
    position: absolute;
    left: 90px;
    top: 100px;
    display: flex;
    align-items: center;
    gap: 16px;
    color: var(--card-white);
  }
  .brand-square {
    width: 44px;
    height: 44px;
    border: 3px solid var(--card-white);
  }
  .brand-name {
    font-family: "Lato", sans-serif;
    font-weight: 700;
    font-size: 50px;
    letter-spacing: 1px;
    line-height: 1;
  }
  .card-back {
    left: 630px;
    background: var(--card-white);
    color: var(--ink-green);
  }
  .contact-block {
    position: absolute;
    left: 34px;
    top: 34px;
  }
  .person-name {
    font-family: "Oswald", sans-serif;
    font-weight: 500;
    font-size: 30px;
    line-height: 1.1;
    text-transform: uppercase;
  }
  .detail-line {
    font-family: "Lato", sans-serif;
    font-weight: 700;
    font-size: 11px;
    line-height: 1.5;
    text-transform: uppercase;
    letter-spacing: 0.3px;
  }
  .salesperson-photo {
    position: absolute;
    left: 34px;
    top: 138px;
    width: 104px;
    height: 118px;
    border: 2px solid var(--ink-green);
    background: linear-gradient(160deg, var(--photo-tint-light), var(--photo-tint-dark));
  }
  .divider {
    position: absolute;
    left: 200px;
    top: 96px;
  }
  .address-block {
    position: absolute;
    left: 256px;
    bottom: 30px;
    width: 216px;
  }
  .phone {
    font-family: "Oswald", sans-serif;
    font-weight: 500;
    font-size: 30px;
    line-height: 1.15;
    margin-bottom: 2px;
  }
</style>
</head>
<body>
<main class="canvas">
  <section class="card card-front" aria-label="Card front">
    <div class="brand">
      <span class="brand-square"></span>
      <span class="brand-name">Fernhale</span>
    </div>
  </section>

  <section class="card card-back" aria-label="Card back">
    <div class="contact-block">
      <h1 class="person-name">Marcus Ellery</h1>
      <p class="detail-line">Chief Executive Officer</p>
      <p class="detail-line">hello@brightlane.com</p>
      <p class="detail-line">www.brightlane.com</p>
    </div>

    <div class="salesperson-photo" role="img" aria-label="Space for a portrait photo of the salesperson"></div>

    <svg class="divider" width="80" height="80" viewBox="0 0 80 80" aria-hidden="true">
      <line x1="4" y1="76" x2="76" y2="4" stroke="var(--ink-green)" stroke-width="3"/>
    </svg>

    <div class="address-block">
      <p class="phone">418 72 306 51</p>
      <p class="detail-line">East 14th Avenue, 3rd Floor,</p>
      <p class="detail-line">Birch Court, Portland</p>
      <p class="detail-line">United States</p>
    </div>
  </section>
</main>
</body>
</html>
```